Phuket Thailand - Rental Villa Website

I have a villa for rent in Thailand and require a website - i need to demo pictures/walk through video, local attractions, villa facilities description plus seaonal rates and online booking.

Industry/Entity Type

Rental

Coding

Coded - Design and coding required

```html
<!DOCTYPE html>
<html lang="en">
<head>
<meta charset="utf-8">
<title>Palm Cove Villa – Service in Phuket, Thailand</title>
<link href="https://fonts.googleapis.com/css2?family=Arimo:wght@400;700&family=Open+Sans:wght@400;600;700&display=swap" rel="stylesheet">
<style>
:root{
  --red:#c8080c;
  --red-dark:#a30000;
  --black:#111;
  --topbar:#0d0d0d;
  --white:#fff;
  --grey-bg:#f1f1f1;
  --rule:#e4e4e4;
  --text:#555;
  --text-dark:#1a1a1a;
  --footer:#161616;
  --footer-bottom:#0b0b0b;
  --footer-text:#bbb;
}
*{margin:0;padding:0;box-sizing:border-box}
html,body{width:679px;height:1200px;overflow:hidden;background:var(--white)}
body{position:relative;font-family:"Arimo",Arial,sans-serif;color:var(--text);font-size:7px}
.abs{position:absolute}

/* top bar */
.topbar{left:0;top:0;width:679px;height:14px;background:var(--topbar)}
.topbar .support{left:182px;top:4px;color:#aaa;font-size:5.5px;display:flex;gap:4px;align-items:center}
.topbar .social{right:0;top:0;display:flex}
.topbar .social span{width:19px;height:14px;border-left:1px solid #333;display:flex;align-items:center;justify-content:center}
.topbar .social i{width:6px;height:6px;background:#999;border-radius:1px;display:block}

/* header */
.header{left:0;top:14px;width:679px;height:38px;background:var(--white)}
.logo{left:56px;top:0;width:107px;height:52px;background:var(--red);color:var(--white);text-align:center;padding-top:12px}
.logo .name{font-size:13px;font-weight:700;letter-spacing:.2px}
.logo .tag{font-size:6.5px;margin-top:4px}
.nav{right:56px;top:30px;display:flex;gap:17px;font-size:7px;color:#333}
.nav .active{color:var(--red)}

/* hero */
.hero{left:0;top:52px;width:679px;height:297px;background:linear-gradient(120deg,#3a2e28 0%,#6e655c 30%,#a8a39a 55%,#8a8f80 75%,#cfcfcf 100%)}
.hero-arrow{top:181px;width:18px;height:42px;background:rgba(0,0,0,.35);display:flex;align-items:center;justify-content:center}
.price-tag{left:56px;top:158px;display:flex;font-size:6px;height:19px}
.price-tag .price{background:var(--red);color:#fff;width:54px;display:flex;align-items:center;justify-content:center}
.price-tag .details{background:#111;color:#fff;width:51px;display:flex;align-items:center;justify-content:center}
.caption{left:56px;top:177px;width:270px;height:60px;background:#fff;padding:13px 14px}
.caption h2{font-size:8px;font-weight:400;color:#111;margin-bottom:4px}
.caption p{font-size:6.2px;line-height:1.65}

/* section titles */
.section-title{font-family:"Open Sans",Arial,sans-serif;font-weight:700;font-size:12px;color:var(--text-dark);letter-spacing:-.2px}
.section-title em{font-style:normal;color:var(--red)}
.title-rule{height:4px;background:var(--rule)}

/* booking */
.booking-form{left:56px;top:393px;display:flex;gap:6px;height:19px}
.field{border:1px solid #ddd;background:#fff;font-size:6px;color:#666;display:flex;align-items:center;justify-content:space-between;padding-left:7px}
.field .caret{width:8px;height:100%;background:#eee;border-left:1px solid #ccc;display:flex;align-items:center;justify-content:center}
.btn-book{background:var(--red);color:#fff;font-weight:700;font-size:6.5px;width:46px;display:flex;align-items:center;justify-content:center}

.grey{left:0;top:438px;width:679px;height:610px;background:var(--grey-bg)}

/* attractions */
.attraction{top:497px;width:134px;height:137px;background:#fff;box-shadow:0 2px 3px rgba(0,0,0,.08)}
.attraction .photo{height:77px}
.attraction p{font-size:6px;line-height:1.7;padding:10px 9px 5px}
.btn{display:inline-flex;align-items:center;justify-content:center;background:var(--red);color:#fff;font-size:6.5px;border-radius:9px;width:40px;height:15px}
.attraction .btn{margin-left:9px}
.pager{display:flex;gap:3px;color:#ccc;font-size:10px}

/* welcome */
.welcome-text{left:56px;top:690px;width:362px}
.welcome-text .lead{font-style:italic;color:#333;font-size:6.2px;line-height:1.85;margin-bottom:7px}
.welcome-text .body{font-size:6.2px;line-height:1.9}
.video{left:452px;top:665px;width:170px;height:113px;background:#111}
.video .frame{position:absolute;left:0;top:13px;width:170px;height:86px;background:linear-gradient(110deg,#4a3a30,#8c8a82 55%,#b8bdb0)}
.video .bar{position:absolute;left:0;bottom:0;width:170px;height:14px;background:#1c1c1c;display:flex;align-items:center;gap:8px;padding-left:10px;color:#ccc;font-size:4.5px}
.video .top{position:absolute;right:8px;top:4px;color:#ddd;font-size:4.5px;display:flex;gap:12px}

/* facilities */
.facility{top:834px;width:137px}
.facility .photo{height:99px;position:relative}
.facility .tag{position:absolute;right:0;top:0;display:flex;height:16px;font-size:8px}
.facility .tag .amt{background:#111;color:#fff;padding:0 8px;display:flex;align-items:center}
.facility .tag .ic{background:var(--red);width:16px;display:flex;align-items:center;justify-content:center}
.facility .meta{height:16px;background:#e8e8e8;display:flex;align-items:center;gap:7px;padding-left:5px;font-size:4px;color:#555}
.facility .meta i{width:4px;height:4px;background:#555;display:inline-block;margin-right:2px;border-radius:1px}
.facility p{font-size:6.2px;line-height:1.85;text-align:justify;padding-top:7px;height:54px}

/* footer */
.footer{left:0;top:1048px;width:679px;height:118px;background:var(--footer);color:var(--footer-text)}
.footer h4{font-family:"Open Sans",Arial,sans-serif;font-weight:700;font-size:7.5px;color:#fff;position:absolute;top:21px}
.links{position:absolute;left:59px;top:43px;list-style:none;font-size:5.5px;line-height:9.7px}
.links li::before{content:"";display:inline-block;width:2.5px;height:2.5px;border-radius:50%;background:#ccc;margin-right:6px;vertical-align:middle}
.newsletter{position:absolute;left:159px;top:46px;width:133px;height:20px;background:#0b0b0b;display:flex;align-items:center;justify-content:space-between;padding:0 3px 0 9px;font-size:5.5px;color:#999}
.newsletter .send{background:var(--red);color:#fff;width:43px;height:15px;display:flex;align-items:center;justify-content:center;font-size:7.5px}
.contact{position:absolute;left:332px;top:45px;font-size:5.5px;line-height:13.5px}
.contact div{display:flex;align-items:center;gap:6px}
.follow{position:absolute;left:478px;top:44px;display:flex;gap:7px}
.follow span{width:15px;height:15px;display:block}
.copyright{left:0;top:1166px;width:679px;height:34px;background:var(--footer-bottom);color:#aaa;font-size:6px;text-align:center;padding-top:12px}
</style>
</head>
<body>

<div class="abs topbar">
  <div class="abs support">
    <svg width="6" height="6" viewBox="0 0 10 10"><path d="M2 1l2 2-1 1.5c.8 1.5 1.7 2.4 3.2 3.2L7.7 6.7l2 2L8.3 10C4 9.5.5 6 0 1.7z" fill="#aaa"/></svg>
    Need Support?&nbsp; 012 345 6789
  </div>
  <div class="abs social"><span><i></i></span><span><i></i></span><span><i></i></span><span><i></i></span><span><i></i></span></div>
</div>

<header class="abs header">
  <nav class="abs nav" style="top:16px">
    <span class="active">Home</span><span>About Us</span><span>Services</span><span>Videos</span><span>Local Attractions</span><span>Villa Facilities</span><span>Contact Us</span>
  </nav>
</header>
<div class="abs logo"><div class="name">Palm Cove Villa</div><div class="tag">Service in Phuket, Thailand</div></div>

<section class="abs hero" role="img" aria-label="Photo of the villa bedroom interior with a garden view"></section>
<div class="abs hero-arrow" style="left:0"><svg width="6" height="9" viewBox="0 0 6 9"><path d="M5 1L1 4.5 5 8" stroke="#fff" fill="none"/></svg></div>
<div class="abs hero-arrow" style="right:0"><svg width="6" height="9" viewBox="0 0 6 9"><path d="M1 1l4 3.5L1 8" stroke="#fff" fill="none"/></svg></div>
<div class="abs price-tag"><div class="price">$ 145.00</div><div class="details">More Details</div></div>
<div class="abs caption">
  <h2>Lorem ipsum dolor sit amet, consectetuer adipiscing elit.</h2>
  <p>Aenean commodo ligula eget dolor. Aenean massa. Cum sociis natoque penati-bus et magnis dis parturient montes.</p>
</div>

<h2 class="abs section-title" style="left:56px;top:364px">ONLINE <em>BOOKING</em></h2>
<div class="abs title-rule" style="left:174px;top:370px;width:452px"></div>
<form class="abs booking-form">
  <div class="field" style="width:118px">Select Room<span class="caret"><svg width="4" height="3"><path d="M0 0h4L2 3z" fill="#333"/></svg></span></div>
  <div class="field" style="width:80px;padding-right:4px">Arrival<svg width="8" height="7"><rect x=".5" y="1" width="7" height="5.5" fill="none" stroke="#aaa"/><path d="M.5 3h7" stroke="#aaa"/></svg></div>
  <div class="field" style="width:81px;padding-right:4px">Departure<svg width="8" height="7"><rect x=".5" y="1" width="7" height="5.5" fill="none" stroke="#aaa"/><path d="M.5 3h7" stroke="#aaa"/></svg></div>
  <div class="field" style="width:73px">Adult<span class="caret"><svg width="4" height="3"><path d="M0 0h4L2 3z" fill="#333"/></svg></span></div>
  <div class="field" style="width:65px">Child<span class="caret"><svg width="4" height="3"><path d="M0 0h4L2 3z" fill="#333"/></svg></span></div>
  <div class="field" style="width:82px">Email Address</div>
  <div class="btn-book">BOOK NOW</div>
</form>

<div class="abs grey"></div>

<h2 class="abs section-title" style="left:56px;top:462px">LOCAL <em>ATTRACTIONS</em></h2>
<div class="abs title-rule" style="left:188px;top:468px;width:405px"></div>
<div class="abs pager" style="left:604px;top:461px"><span>‹</span><span>›</span></div>

<article class="abs attraction" style="left:56px"><div class="photo" role="img" aria-label="Villa roof and garden" style="background:linear-gradient(135deg,#5b7a3c,#8a6a58 60%,#cfd2d4)"></div><p>Lorem ipsum dolor sit amet, consectetuer adipiscing elit&nbsp; aenean commodo</p><span class="btn">More</span></article>
<article class="abs attraction" style="left:200px"><div class="photo" role="img" aria-label="Terrace overlooking the hills" style="background:linear-gradient(160deg,#b9c0c6,#6f7d62 55%,#5a4a3c)"></div><p>Lorem ipsum dolor sit amet, consectetuer adipiscing elit&nbsp; aenean commodo</p><span class="btn">More</span></article>
<article class="abs attraction" style="left:345px"><div class="photo" role="img" aria-label="Infinity pool with mountain view" style="background:linear-gradient(180deg,#c7ccd0,#6a7a62 35%,#8e9a98 60%,#a9aea8)"></div><p>Lorem ipsum dolor sit amet, consectetuer adipiscing elit&nbsp; aenean commodo</p><span class="btn">More</span></article>
<article class="abs attraction" style="left:490px"><div class="photo" role="img" aria-label="Open veranda with timber roof" style="background:linear-gradient(170deg,#4a3526,#8c7c6c 50%,#d8dcd8)"></div><p>Lorem ipsum dolor sit amet, consectetuer adipiscing elit&nbsp; aenean commodo</p><span class="btn">More</span></article>

<h2 class="abs section-title" style="left:56px;top:659px">WELCOME TO&nbsp; <em>PALM COVE VILLA</em></h2>
<div class="abs welcome-text">
  <p class="lead">Lorem ipsum dolor sit amet, consectetuer adipiscing elit. Aenean commodo ligula eget dolor. Aenean massa. Cum sociis natoque penatibus et magnis dis parturient montes, nascetur ridiculus mus.</p>
  <p class="body">Donec quam felis, ultricies nec, pellentesque eu, pretium quis, sem. Nulla consequat massa quis enim. Donec pede justo, fringilla vel, aliquet nec,Vulputate eget, arcu. In enim justo, rhoncus ut, imperdiet a, venenatis vitae, justo. Nullam dictum felis eu pede mollis pretium. Integer tincidunt. Cras dapibus. Vivamus elementum semper nisi.</p>
</div>
<span class="abs btn" style="left:56px;top:762px">More</span>

<div class="abs video">
  <div class="top"><span>Share</span><span>More info</span></div>
  <div class="frame" role="img" aria-label="Walk-through video of the villa interior"></div>
  <svg class="abs" style="left:73px;top:44px" width="24" height="24" viewBox="0 0 24 24"><rect width="24" height="24" rx="3" fill="#c8080c"/><path d="M9 6l9 6-9 6z" fill="#fff"/></svg>
  <div class="bar"><svg width="6" height="6"><path d="M0 0l6 3-6 3z" fill="#aaa"/></svg><span>◂◂)</span><span>0:00 / 0:00</span></div>
</div>

<h2 class="abs section-title" style="left:59px;top:800px">VILLA <em>FACILITIES</em></h2>
<div class="abs title-rule" style="left:168px;top:806px;width:425px"></div>
<div class="abs pager" style="left:604px;top:799px"><span style="color:#111">‹</span><span>›</span></div>

<article class="abs facility" style="left:56px"><div class="photo" role="img" aria-label="Terrace with mountain view" style="background:linear-gradient(160deg,#b8c0c4,#5f7550 45%,#7a6250 70%,#c8c4bc)"><div class="tag"><span class="amt">$ 100,000/-</span><span class="ic"><svg width="8" height="8" viewBox="0 0 8 8"><path d="M0 0h4l4 4-4 4-4-4z" fill="#fff"/></svg></span></div></div><div class="meta"><span><i></i>20,000 Acres</span><span><i></i>3 Bedrooms</span><span><i></i>3 Bathrooms</span></div><p>Lorem ipsum dolor sit amet, consectetuer adipiscing elit. Aenean commodo ligula eget dolor. Aenean massa.</p><span class="btn">More</span></article>
<article class="abs facility" style="left:199px"><div class="photo" role="img" aria-label="Bedroom with double bed" style="background:linear-gradient(150deg,#6e6860,#c8c2b8 50%,#7d7f92)"><div class="tag"><span class="amt">$ 100,000/-</span><span class="ic"><svg width="8" height="8" viewBox="0 0 8 8"><path d="M0 0h4l4 4-4 4-4-4z" fill="#fff"/></svg></span></div></div><div class="meta"><span><i></i>20,000 Acres</span><span><i></i>3 Bedrooms</span><span><i></i>3 Bathrooms</span></div><p>Lorem ipsum dolor sit amet, consectetuer adipiscing elit. Aenean commodo ligula eget dolor. Aenean massa.</p><span class="btn">More</span></article>
<article class="abs facility" style="left:342px"><div class="photo" role="img" aria-label="Villa exterior with tiled roof" style="background:linear-gradient(135deg,#cfd3d6,#4c4c52 40%,#8a5f4c 70%,#9a7a62)"><div class="tag"><span class="amt">$ 100,000/-</span><span class="ic"><svg width="8" height="8" viewBox="0 0 8 8"><path d="M0 0h4l4 4-4 4-4-4z" fill="#fff"/></svg></span></div></div><div class="meta"><span><i></i>20,000 Acres</span><span><i></i>3 Bedrooms</span><span><i></i>3 Bathrooms</span></div><p>Lorem ipsum dolor sit amet, consectetuer adipiscing elit. Aenean commodo ligula eget dolor. Aenean massa.</p><span class="btn">More</span></article>
<article class="abs facility" style="left:486px"><div class="photo" role="img" aria-label="Covered outdoor veranda" style="background:linear-gradient(170deg,#5a4030,#8e7e6e 45%,#e2e2de)"><div class="tag"><span class="amt">$ 100,000/-</span><span class="ic"><svg width="8" height="8" viewBox="0 0 8 8"><path d="M0 0h4l4 4-4 4-4-4z" fill="#fff"/></svg></span></div></div><div class="meta"><span><i></i>20,000 Acres</span><span><i></i>3 Bedrooms</span><span><i></i>3 Bathrooms</span></div><p>Lorem ipsum dolor sit amet, consectetuer adipiscing elit. Aenean commodo ligula eget dolor. Aenean massa.</p><span class="btn">More</span></article>

<footer class="abs footer">
  <h4 style="left:59px">QUICK LINKS</h4>
  <ul class="links"><li>Home</li><li>About Us</li><li>Services</li><li>Videos</li><li>Local Attractions</li><li>Villa Facilities</li><li>Contact Us</li></ul>
  <h4 style="left:158px">NEWSLETTER SIGNUP</h4>
  <div class="newsletter">Enter your email here<span class="send">Send</span></div>
  <h4 style="left:332px">CONTACT</h4>
  <div class="contact">
    <div><svg width="8" height="7" viewBox="0 0 8 7"><path d="M0 1h8v2H6V2H2v1H0zM1 3.5h6V7H1z" fill="#aaa"/></svg>Phone: (012) 3456 7788 990</div>
    <div><svg width="8" height="6" viewBox="0 0 8 6"><rect x=".5" y=".5" width="7" height="5" fill="none" stroke="#aaa"/><path d="M.5.5L4 3.5 7.5.5" stroke="#aaa" fill="none"/></svg>Email: info@palmcovevilla.example</div>
    <div><svg width="8" height="9" viewBox="0 0 8 9"><path d="M4 0a3.5 3.5 0 0 1 3.5 3.5C7.5 6 4 9 4 9S.5 6 .5 3.5A3.5 3.5 0 0 1 4 0z" fill="#aaa"/><circle cx="4" cy="3.5" r="1.3" fill="#161616"/></svg>Address: Street Name ,City</div>
    <div style="padding-left:14px">Street Name ,City</div>
  </div>
  <h4 style="left:478px">FOLLOW US ON</h4>
  <div class="follow">
    <span style="background:#3b5a9a"></span><span style="background:#2a9fd6"></span><span style="background:#d8201c"></span><span style="background:#f0861c"></span><span style="background:#d23a2c"></span><span style="background:#1a5c9a"></span>
  </div>
</footer>
<div class="abs copyright">Copyright 2014&nbsp; PALM COVE VILLA |&nbsp; All Rights Reserved.</div>

</body>
</html>
```